VOMRA Pty Ltd Business Card

Looking for a simple yet eye-catching double-sided business card design using my company logo on one side and contact details on the other.

Target Market(s)

Government

Industry/Entity Type

Communication Systems Engineering

Contact Information for Business Card

VOMRA Pty Ltd

Requirements
Nice to have
• Would be great to have a QR code so details can be scanned into contacts

```html
<!DOCTYPE html>
<html lang="en">
<head>
<meta charset="utf-8">
<title>VOMRA Pty Ltd Business Card</title>
<link href="https://fonts.googleapis.com/css2?family=Open+Sans:wght@400;600;700&display=swap" rel="stylesheet">
<style>
  :root {
    --backdrop: #232323;
    --slate: #37424a;
    --slate-deep: #2c353c;
    --paper: #ffffff;
    --ink: #2f3a42;
    --ink-soft: #1e262c;
  }
  * { box-sizing: border-box; margin: 0; padding: 0; }
  html, body { width: 1200px; height: 780px; overflow: hidden; }
  body {
    background: var(--backdrop);
    font-family: "Open Sans", sans-serif;
    display: flex;
    align-items: center;
    justify-content: center;
    gap: 80px;
  }
  .card {
    width: 360px;
    height: 580px;
    border-radius: 0 150px 0 150px;
    position: relative;
    box-shadow: 0 18px 40px rgba(0,0,0,0.55);
  }
  .card--front { background: var(--slate); }
  .card--back { background: var(--paper); color: var(--ink); }

  .front-brand {
    position: absolute;
    inset: 0;
    display: flex;
    align-items: center;
    justify-content: center;
    gap: 16px;
  }
  .front-brand__dot {
    width: 26px; height: 26px;
    border-radius: 50%;
    background: var(--slate-deep);
  }
  .front-brand__name {
    font-weight: 700;
    font-size: 64px;
    letter-spacing: 4px;
    color: var(--slate-deep);
  }

  .back-brand {
    position: absolute;
    top: 66px;
    left: 50px;
    display: flex;
    align-items: center;
    gap: 14px;
  }
  .back-brand__dot {
    width: 20px; height: 20px;
    border-radius: 50%;
    background: var(--ink);
  }
  .back-brand__name {
    font-weight: 700;
    font-size: 46px;
    letter-spacing: 3px;
    color: var(--ink);
  }

  .contact {
    position: absolute;
    left: 0; right: 0;
    top: 286px;
    text-align: center;
  }
  .contact__name { font-weight: 700; font-size: 30px; line-height: 1.1; }
  .contact__role { font-weight: 600; font-size: 15px; margin-top: 2px; color: var(--ink-soft); }
  .contact__icons {
    display: flex;
    justify-content: center;
    gap: 6px;
    margin: 12px 0 6px;
  }
  .icon {
    width: 24px; height: 24px;
    border-radius: 50%;
    background: var(--ink);
    display: flex; align-items: center; justify-content: center;
  }
  .icon svg { width: 14px; height: 14px; }
  .contact__line { font-size: 16px; line-height: 1.35; color: var(--ink-soft); }
  .contact__pin { margin: 14px auto 14px; }
  .contact__address { font-size: 16px; line-height: 1.35; color: var(--ink-soft); }
</style>
</head>
<body>
  <section class="card card--front" aria-label="Card front">
    <div class="front-brand">
      <span class="front-brand__dot"></span>
      <span class="front-brand__name">VOMRA</span>
    </div>
  </section>

  <section class="card card--back" aria-label="Card back">
    <div class="back-brand">
      <span class="back-brand__dot"></span>
      <span class="back-brand__name">VOMRA</span>
    </div>

    <div class="contact">
      <p class="contact__name">Jordan Pell</p>
      <p class="contact__role">Co-Founder</p>
      <div class="contact__icons">
        <span class="icon" aria-label="Phone">
          <svg viewBox="0 0 24 24"><path fill="#fff" d="M6.6 10.8a15 15 0 0 0 6.6 6.6l2.2-2.2c.3-.3.7-.4 1-.2 1.1.4 2.3.6 3.6.6.6 0 1 .4 1 1V20c0 .6-.4 1-1 1A17 17 0 0 1 3 4c0-.6.4-1 1-1h3.5c.6 0 1 .4 1 1 0 1.3.2 2.5.6 3.6.1.3 0 .7-.2 1z"/></svg>
        </span>
        <span class="icon" aria-label="Email">
          <svg viewBox="0 0 24 24"><rect x="3" y="6" width="18" height="12" rx="1.5" fill="none" stroke="#fff" stroke-width="2"/><path d="M3.5 7l8.5 6 8.5-6" fill="none" stroke="#fff" stroke-width="2"/></svg>
        </span>
        <span class="icon" aria-label="Website">
          <svg viewBox="0 0 24 24"><circle cx="12" cy="12" r="9" fill="none" stroke="#fff" stroke-width="2"/><ellipse cx="12" cy="12" rx="4" ry="9" fill="none" stroke="#fff" stroke-width="1.6"/><path d="M3 12h18" stroke="#fff" stroke-width="1.6"/></svg>
        </span>
      </div>
      <p class="contact__line">(555) 014-2290</p>
      <p class="contact__line">www.vomra.com.au</p>
      <p class="contact__line">admin@vomra.com.au</p>
      <span class="icon contact__pin" aria-label="Address">
        <svg viewBox="0 0 24 24"><path fill="#fff" d="M12 2a7 7 0 0 0-7 7c0 5 7 13 7 13s7-8 7-13a7 7 0 0 0-7-7zm0 9.5A2.5 2.5 0 1 1 12 6.5a2.5 2.5 0 0 1 0 5z"/></svg>
      </span>
      <p class="contact__address">14-16 Harlow Street Easton<br>Vale NSW 2099 Australia</p>
    </div>
  </section>
</body>
</html>
```